New Business Cards for Tormin Group

We need a new Business Card to compliment our new logo. We are a vibrant design, manufacture and install business providing recreation areas, public parks and Municipal spaces. We want business cards that are classy, modern and clean.

We have recently changed our logo, and are celebrating our 40th anniversary. We want business cards with a new modern design to reflect our status.

Target Market(s)

Customers

Contact Information for Business Card

We need all the details of our 3 offices as per the business card attached. Please disregard the old logo on the business card, the other three files show our new logo.

Requirements
Must have
• All info as per attached business card but with new logo.
Nice to have

```html
<!DOCTYPE html>
<html lang="en">
<head>
<meta charset="utf-8">
<title>Tormin Group – Business Cards</title>
<link href="https://fonts.googleapis.com/css2?family=Source+Sans+3:wght@400;600;700&display=swap" rel="stylesheet">
<style>
  :root {
    --backdrop: #d5d5d5;
    --card: #48494b;
    --red: #e8323a;
    --white: #ffffff;
    --soft: #e6e6e6;
  }
  * { box-sizing: border-box; margin: 0; padding: 0; }
  html, body { width: 1200px; height: 900px; overflow: hidden; }
  body {
    background: var(--backdrop);
    font-family: "Source Sans 3", sans-serif;
    color: var(--white);
    display: flex;
    align-items: center;
    justify-content: center;
    gap: 40px;
  }
  .card {
    width: 540px;
    height: 309px;
    background: var(--card);
    box-shadow: 0 4px 14px rgba(0,0,0,0.25);
    position: relative;
  }
  /* front */
  .card-front { display: flex; align-items: center; justify-content: center; }
  .brand { display: flex; align-items: center; gap: 14px; }
  .brand-dot { border-radius: 50%; background: var(--red); flex: none; }
  .brand-name { font-weight: 700; color: var(--white); text-transform: uppercase; letter-spacing: 0.04em; line-height: 1; }
  .card-front .brand-dot { width: 70px; height: 70px; }
  .card-front .brand-name { font-size: 40px; }

  /* back */
  .card-back { display: flex; padding: 30px 28px 26px 30px; gap: 26px; }
  .identity { width: 230px; display: flex; flex-direction: column; }
  .identity .brand { gap: 10px; }
  .identity .brand-dot { width: 34px; height: 34px; }
  .identity .brand-name { font-size: 21px; }
  .established { font-size: 10px; letter-spacing: 0.08em; color: var(--soft); margin: 4px 0 0 44px; }
  .person-name { color: var(--red); font-size: 18px; font-weight: 400; margin-top: 20px; line-height: 1.1; }
  .person-role { font-size: 12.5px; color: var(--soft); margin-bottom: 10px; }
  .contact-line { display: flex; align-items: center; gap: 7px; font-size: 12.5px; line-height: 1.45; color: var(--white); }
  .icon { width: 11px; height: 11px; flex: none; fill: none; stroke: var(--red); stroke-width: 1.6; }
  .icon.solid { fill: var(--red); stroke: none; }
  .company-lines { margin-top: auto; }
  .web-accent { color: var(--red); }
  .web-line { padding-left: 18px; }

  .offices { flex: 1; display: flex; flex-direction: column; justify-content: space-between; padding-left: 14px; border-left: 1px solid rgba(255,255,255,0.12); }
  .office-title { font-size: 13px; font-weight: 700; }
  .office-address { font-size: 12px; color: var(--soft); line-height: 1.35; }
  .office .contact-line { font-size: 12px; line-height: 1.35; }
</style>
</head>
<body>
  <svg width="0" height="0" style="position:absolute">
    <defs>
      <symbol id="icon-phone" viewBox="0 0 12 12"><path d="M2.5 1 L4.5 1 L5.2 3.6 L3.9 4.6 Q5 7 7.4 8.1 L8.4 6.8 L11 7.5 L11 9.5 Q10.5 11 8.8 11 Q1 9.5 1 3.2 Q1 1.5 2.5 1 Z"/></symbol>
      <symbol id="icon-fax" viewBox="0 0 12 12"><rect x="3" y="1" width="6" height="3"/><rect x="1" y="4" width="10" height="5" rx="1"/><rect x="3" y="8" width="6" height="3"/></symbol>
      <symbol id="icon-mobile" viewBox="0 0 12 12"><rect x="3" y="1" width="6" height="10" rx="1"/></symbol>
      <symbol id="icon-mail" viewBox="0 0 12 12"><rect x="1" y="2.5" width="10" height="7"/><path d="M1 2.5 L6 6.5 L11 2.5"/></symbol>
    </defs>
  </svg>

  <section class="card card-front" aria-label="Card front">
    <div class="brand">
      <span class="brand-dot"></span>
      <span class="brand-name">Tormin Group</span>
    </div>
  </section>

  <section class="card card-back" aria-label="Card back">
    <div class="identity">
      <div class="brand">
        <span class="brand-dot"></span>
        <span class="brand-name">Tormin Group</span>
      </div>
      <p class="established">EST. 1979</p>
      <h1 class="person-name">Rami Kassem</h1>
      <p class="person-role">Managing Partner</p>
      <p class="contact-line"><svg class="icon"><use href="#icon-mobile"/></svg>+971 (0)50 000 4812</p>
      <p class="contact-line"><svg class="icon"><use href="#icon-mail"/></svg>rami@tormingroup.com</p>
      <div class="company-lines">
        <p class="contact-line"><svg class="icon"><use href="#icon-mail"/></svg>sales@tormingroup.com</p>
        <p class="contact-line web-line">www.<span class="web-accent">tormingroup</span>.com</p>
      </div>
    </div>

    <div class="offices">
      <div class="office">
        <h2 class="office-title">Head Office:</h2>
        <p class="office-address">P.O. Box: 10482 Abu Dhabi, U.A.E.</p>
        <p class="contact-line"><svg class="icon solid"><use href="#icon-phone"/></svg>+971 (0)2 5550140</p>
        <p class="contact-line"><svg class="icon solid"><use href="#icon-fax"/></svg>+971 (0)2 5550141</p>
      </div>
      <div class="office">
        <h2 class="office-title">Dubai Office:</h2>
        <p class="office-address">P.O. Box: 204718 Dubai, U.A.E.</p>
        <p class="contact-line"><svg class="icon solid"><use href="#icon-phone"/></svg>+971 (0)4 5550172</p>
        <p class="contact-line"><svg class="icon solid"><use href="#icon-fax"/></svg>+971 (0)4 5550173</p>
      </div>
      <div class="office">
        <h2 class="office-title">Qatar Office:</h2>
        <p class="office-address">P.O. Box: 30917 Doha, Qatar</p>
        <p class="contact-line"><svg class="icon solid"><use href="#icon-phone"/></svg>+974 55500218</p>
        <p class="contact-line"><svg class="icon solid"><use href="#icon-fax"/></svg>+974 55500219</p>
      </div>
    </div>
  </section>
</body>
</html>
```